New business card for a regional office of a US M&A company

We need business card for a finance company, office based in Hong Kong , our Head office is in US, our business is to Merge and acquires companies , the new office will be a regional office for the Asia Pacific region. We want to use the head office logo as attached ( but don't have to be exactly the same, can be a variation to it) as a base and then add Asia Pacific alongside the logo.
We would prefer to have be bilingual Eng + Chinese, although we don't really have Chinese company name .

Industry/Entity Type

Business

Contact Information for Business Card

Clara Jo Tsang
 

VP,
APAC M&A Operations
Orin Vantage Asia Pacific Limited
 
Unit 1407, K18
18 Tai Lok Shan Road, 
Hong Kong 
 
M: +852 6038 1742
T : +852 2836 4100
F : +852 2836 4177
VOIP: 4158
 
cjtsang@orinvantage.com

Font styles to use
Serif
Sans Serif

Colors

Designer to choose colors to be used in the design.

Requirements
Must have
• APAC Office

```html
<!DOCTYPE html>
<html lang="en">
<head>
<meta charset="utf-8">
<title>Orin Vantage – APAC Business Card</title>
<link href="https://fonts.googleapis.com/css2?family=Open+Sans:wght@400;600;700;800&display=swap" rel="stylesheet">
<style>
  :root{
    --teal:#07a9c6;
    --navy:#14284a;
    --ink:#555d66;
    --paper:#ffffff;
    --table:#d9dadb;
  }
  *{box-sizing:border-box;margin:0;padding:0}
  html,body{width:1200px;height:800px;overflow:hidden}
  body{background:var(--table);font-family:"Open Sans",Arial,sans-serif;position:relative}
  .card{position:absolute;top:245px;width:540px;height:309px;box-shadow:0 6px 18px rgba(0,0,0,.18);overflow:hidden}
  .card--front{left:40px;background:var(--paper)}
  .card--back{left:620px;background:var(--teal)}

  /* front */
  .wordmark{position:absolute;left:34px;top:112px;font-weight:800;font-size:30px;line-height:1;letter-spacing:.5px;color:var(--teal);white-space:nowrap}
  .identity{position:absolute;right:34px;top:40px;text-align:right}
  .identity__name{font-weight:600;font-size:18px;line-height:1.2;color:var(--navy);text-transform:uppercase;letter-spacing:.3px}
  .identity__title{font-size:12px;color:var(--navy);margin-top:2px}
  .divider{position:absolute;left:30px;right:34px;top:160px;height:1.5px;background:var(--teal)}
  .office{position:absolute;right:34px;top:84px;text-align:right;color:var(--ink);font-size:12px;line-height:1.45}
  .office__voip{font-weight:600;color:var(--navy);margin-bottom:6px}
  .contacts{position:absolute;left:40px;top:178px;list-style:none;color:var(--ink);font-size:12.5px;line-height:1.45}
  .contacts li{display:flex;align-items:center;gap:9px}
  .contacts svg{width:11px;height:11px;flex:none}
  .edge{position:absolute;left:0;right:0;bottom:0;height:8px}
  .edge__navy{position:absolute;left:0;bottom:0;width:300px;height:8px;background:var(--navy)}
  .edge__teal{position:absolute;left:292px;right:0;bottom:0;height:8px;background:var(--teal);clip-path:polygon(8px 0,100% 0,100% 100%,0 100%)}

  /* back */
  .back-mark{position:absolute;left:50%;top:78px;transform:translateX(-50%);width:58px;height:58px;border:7px solid var(--paper)}
  .back-wordmark{position:absolute;left:0;right:0;top:158px;text-align:center;font-weight:800;font-size:44px;letter-spacing:1px;color:var(--paper)}
</style>
</head>
<body>
  <section class="card card--front" aria-label="Business card, front">
    <div class="identity">
      <div class="identity__name">Clara Jo Tsang</div>
      <div class="identity__title">VP, APAC M&amp;A Operations</div>
    </div>
    <div class="office">
      <div class="office__voip">VOIP: 4158</div>
      <div>Unit 1407, K18 18 Tai Lok Shan</div>
      <div>Road, Hong Kong</div>
    </div>
    <div class="wordmark">ORIN VANTAGE</div>
    <div class="divider"></div>
    <ul class="contacts">
      <li><svg viewBox="0 0 12 12"><rect x="3" y="0.5" width="6" height="11" rx="1" fill="none" stroke="#07a9c6" stroke-width="1.2"/></svg>+852 6038 1742</li>
      <li><svg viewBox="0 0 12 12"><path d="M2 1l2.5 0 1 3-1.5 1c.8 1.6 1.8 2.6 3 3l1-1.5 3 1V11C6 11 1 6 2 1z" fill="#07a9c6"/></svg>+852 2836 4100</li>
      <li><svg viewBox="0 0 12 12"><rect x="3" y="0.5" width="6" height="4" fill="#07a9c6"/><rect x="1" y="4.5" width="10" height="6" rx="1" fill="#07a9c6"/></svg>+852 2836 4177</li>
      <li><svg viewBox="0 0 12 12"><rect x="0.5" y="2" width="11" height="8" fill="#07a9c6"/><path d="M0.5 2l5.5 4.5L11.5 2" fill="none" stroke="#fff" stroke-width="1.1"/></svg>cjtsang@orinvantage.com</li>
    </ul>
    <div class="edge"><div class="edge__navy"></div><div class="edge__teal"></div></div>
  </section>

  <section class="card card--back" aria-label="Business card, back">
    <div class="back-mark"></div>
    <div class="back-wordmark">ORIN VANTAGE</div>
  </section>
</body>
</html>
```